Harrow Grading LLC business card design

Excavation company business cards

Contact Information for Business Card

Harrow Grading LLC cell phone 208-417-6290 office phone 208-319-4856 harrowgradingllc@maplecove.com Driveways, site prep, retaining walls, septic systems, rock delivery

Colors

Designer to choose colors to be used in the design.

```html
<!DOCTYPE html>
<html lang="en">
<head>
<meta charset="utf-8">
<title>Harrow Grading LLC – Business Card</title>
<link rel="stylesheet" href="https://fonts.googleapis.com/css2?family=Poppins:wght@700&family=Roboto:ital,wght@0,400;0,500;1,400&display=swap">
<style>
  :root {
    --bg: #dcdcdc;
    --card-light: #ffffff;
    --card-dark: #1c1c1c;
    --orange: #ee6c22;
    --ink: #222222;
    --rule: #777777;
    --white: #ffffff;
  }
  * { margin: 0; padding: 0; box-sizing: border-box; }
  html, body { width: 1200px; height: 1200px; overflow: hidden; background: var(--bg); }
  .canvas { position: relative; width: 1200px; height: 1200px; }
  .card {
    position: absolute; top: 240px; width: 420px; height: 720px;
    border-radius: 34px; overflow: hidden;
  }
  .card--front { left: 150px; background: var(--card-light); }
  .card--back { left: 630px; background: var(--card-dark); }

  .brand {
    position: absolute; top: 150px; left: 0; width: 100%;
    text-align: center; font-family: "Poppins", sans-serif; font-weight: 700;
    color: var(--orange); font-size: 34px; line-height: 1.15; letter-spacing: 1px;
  }
  .person { position: absolute; top: 395px; left: 0; width: 100%; text-align: center; font-family: "Roboto", sans-serif; }
  .person__name { color: var(--orange); font-weight: 500; font-size: 30px; letter-spacing: 1px; }
  .person__role { color: var(--ink); font-style: italic; font-size: 20px; margin-top: 2px; }

  .icon-row {
    position: absolute; top: 490px; left: 30px; right: 30px;
    display: flex; align-items: center; gap: 10px;
  }
  .icon-row__rule { flex: 1; height: 1px; background: var(--rule); }
  .icon { width: 24px; height: 24px; border-radius: 4px; background: var(--orange); display: flex; align-items: center; justify-content: center; }
  .icon svg { width: 16px; height: 16px; }

  .contact {
    position: absolute; top: 535px; left: 0; width: 100%; text-align: center;
    font-family: "Roboto", sans-serif; color: var(--ink); font-size: 19px; line-height: 1.45;
  }
  .contact__tag { color: var(--orange); font-size: 14px; }

  .brand--back {
    top: 290px; font-size: 46px; line-height: 1.1; color: var(--orange); letter-spacing: 2px;
  }
  .brand--back .brand__sub { display: block; color: var(--white); font-size: 20px; letter-spacing: 8px; margin-top: 10px; }
</style>
</head>
<body>
<main class="canvas">
  <section class="card card--front">
    <div class="brand">HARROW<br>GRADING LLC</div>
    <div class="person">
      <div class="person__name">DALEN MORROW</div>
      <div class="person__role">Founder</div>
    </div>
    <div class="icon-row">
      <span class="icon-row__rule"></span>
      <span class="icon" aria-label="phone"><svg viewBox="0 0 16 16"><path fill="#fff" d="M3 1.5l2.5 0 1 3.5-1.5 1.2c.8 1.8 2 3 3.8 3.8L10 8.5l3.5 1v2.5c0 .8-.7 1.5-1.5 1.5C6.5 13.5 2.5 9.5 1.5 4 1.5 2.2 2.2 1.5 3 1.5z"/></svg></span>
      <span class="icon" aria-label="mobile"><svg viewBox="0 0 16 16"><rect x="4.5" y="1.5" width="7" height="13" rx="1.3" fill="none" stroke="#fff" stroke-width="1.5"/><circle cx="8" cy="12" r=".9" fill="#fff"/></svg></span>
      <span class="icon" aria-label="email"><svg viewBox="0 0 16 16"><rect x="1.5" y="3.5" width="13" height="9" fill="none" stroke="#fff" stroke-width="1.4"/><path d="M1.5 3.5l6.5 5 6.5-5" fill="none" stroke="#fff" stroke-width="1.4"/></svg></span>
      <span class="icon" aria-label="website"><svg viewBox="0 0 16 16"><circle cx="8" cy="8" r="6" fill="none" stroke="#fff" stroke-width="1.4"/><path d="M2 8h12M8 2c-2.5 3-2.5 9 0 12M8 2c2.5 3 2.5 9 0 12" fill="none" stroke="#fff" stroke-width="1.1"/></svg></span>
      <span class="icon-row__rule"></span>
    </div>
    <div class="contact">
      <div>208-319-4856 <span class="contact__tag">(office)</span></div>
      <div>208-417-6290</div>
      <div>harrowgradingllc@maplecove.com</div>
      <div>www.harrowgradingllc.com</div>
    </div>
  </section>

  <section class="card card--back">
    <div class="brand brand--back">HARROW<br>GRADING<span class="brand__sub">LLC</span></div>
  </section>
</main>
</body>
</html>
```